Brindle Sky Port needs a new upscale business card design for our high end aircraft hangar complex

Brindle Sky Port (BSP) is a large, upscale jet hangar complex in the US housing expensive aircraft. We need a new business card design, using our current logo. We will be attending a industry convention and need a card design that will stand out and be remembered by aircraft owners and private pilots.

Target Market(s)

Aircraft pilots or owners looking for a new upscale hangar

Industry/Entity Type

Airport

Contact Information for Business Card

I like to use very heavy card stock, 400#, double sided. Square, no rounded edges please.

Colors
3276b5
0255a3
85abd2

Requirements
Must have
• An expensive, classy design, vivid colors.
Nice to have
• Needs to look very expensive and classy, and have some "pop". Designer must be able to download or copy my current typeface or fonts.
• One card side might be black with the "Logo and Brindle Sky Port Double line image in blue (or try gold, or glossy black), and perhaps have a grayed out "K720 jet silhouette". The other card side would have our contact info, and perhaps the "BSP Logo only". I'd like my contact info 'stacked', not in a paragraph format.
Should not have
• Should not look "too busy". Having a double-sided card will help.

```html
<!DOCTYPE html>
<html lang="en">
<head>
<meta charset="utf-8">
<title>Brindle Sky Port — Business Card</title>
<link href="https://fonts.googleapis.com/css2?family=Arimo:wght@400;700&display=swap" rel="stylesheet">
<style>
  :root {
    --page-bg: #8c8c8c;
    --card-black: #0f0f10;
    --brand-blue: #2f6aa8;
    --name-blue: #3b78b5;
    --band-light: #245a92;
    --band-dark: #0d2b4f;
    --band-edge: #b9bcc0;
    --text-light: #e8edf3;
    --text-muted: #d6d6d6;
  }
  * { margin: 0; padding: 0; box-sizing: border-box; }
  html, body {
    width: 1105px; height: 1200px; overflow: hidden;
    background: var(--page-bg);
    font-family: "Arimo", Arial, sans-serif;
  }
  .card {
    position: absolute; left: 182px;
    width: 748px; height: 427px;
    background: var(--card-black);
    overflow: hidden;
  }
  .card--front { top: 119px; }
  .card--back { top: 635px; }

  .holder { position: absolute; left: 39px; top: 84px; }
  .holder__name { color: var(--name-blue); font-size: 24px; font-weight: 400; line-height: 30px; }
  .holder__title { color: var(--text-light); font-size: 20px; line-height: 26px; }

  .wordmark {
    position: absolute; text-align: center;
    color: var(--brand-blue); font-weight: 700;
  }
  .wordmark__short { display: block; font-size: 96px; line-height: 100px; letter-spacing: 4px; }
  .wordmark__long { display: block; font-size: 27px; line-height: 34px; letter-spacing: 2px; text-transform: uppercase; }
  .card--front .wordmark { left: 440px; width: 280px; top: 46px; }
  .card--back .wordmark { left: 224px; width: 300px; top: 134px; }

  .band { position: absolute; left: 0; top: 0; width: 748px; height: 427px; }

  .contact-list { position: absolute; left: 38px; top: 284px; list-style: none; }
  .contact-list li {
    display: flex; align-items: center; height: 28.5px;
    color: var(--text-light); font-size: 19px;
  }
  .contact-list svg { width: 20px; height: 20px; margin-right: 17px; fill: var(--text-light); }

  .address {
    position: absolute; right: 40px; top: 292px; text-align: right;
    color: var(--text-light); font-size: 18px; line-height: 26px; font-style: normal;
  }
  .address__web { letter-spacing: 1px; margin-top: 2px; display: block; }

  .back-web {
    position: absolute; left: 0; width: 100%; top: 358px; text-align: center;
    color: var(--text-muted); font-size: 18px; letter-spacing: 5px;
  }
</style>
</head>
<body>

<section class="card card--front" aria-label="Card front">
  <svg class="band" viewBox="0 0 748 427" aria-hidden="true">
    <defs>
      <radialGradient id="bandGlow" cx="0.45" cy="0.75" r="0.7">
        <stop offset="0" stop-color="var(--band-light)"/>
        <stop offset="1" stop-color="var(--band-dark)"/>
      </radialGradient>
    </defs>
    <path d="M0,254 L688,254 Q748,254 748,314 L748,427 L0,427 Z" fill="url(#bandGlow)"/>
    <path d="M0,250 L688,250 Q750,250 750,312" fill="none" stroke="var(--band-edge)" stroke-width="4"/>
  </svg>

  <div class="holder">
    <p class="holder__name">Dana Whitlow</p>
    <p class="holder__title">President</p>
  </div>

  <div class="wordmark">
    <span class="wordmark__short">BSP</span>
    <span class="wordmark__long">Brindle Sky Port</span>
  </div>

  <ul class="contact-list">
    <li><svg viewBox="0 0 20 20" aria-label="Phone"><path d="M2 7c0-3 3-4 8-4s8 1 8 4v1h-4V6H6v2H2z"/><rect x="4" y="9" width="12" height="8" rx="1"/></svg>512 4086 7731</li>
    <li><svg viewBox="0 0 20 20" aria-label="Mobile"><path d="M6 1h8a1 1 0 0 1 1 1v16a1 1 0 0 1-1 1H6a1 1 0 0 1-1-1V2a1 1 0 0 1 1-1zm1 2v12h6V3z"/></svg>734 2619 8840</li>
    <li><svg viewBox="0 0 20 20" aria-label="Fax"><rect x="5" y="2" width="10" height="5"/><rect x="2" y="8" width="16" height="7" rx="1"/><rect x="5" y="13" width="10" height="5"/></svg>608 5172 4409</li>
    <li><svg viewBox="0 0 20 20" aria-label="Email"><path d="M2 5h16v10H2z M2 5l8 6 8-6" fill="none" stroke="var(--text-light)" stroke-width="2"/></svg>dana@brindlesky.com</li>
  </ul>

  <address class="address">
    2170 Harrow Lane<br>
    Cedar Bluff<br>
    NY 11420
    <span class="address__web">www.brindlesky.com</span>
  </address>
</section>

<section class="card card--back" aria-label="Card back">
  <div class="wordmark">
    <span class="wordmark__short">BSP</span>
    <span class="wordmark__long">Brindle Sky Port</span>
  </div>
  <p class="back-web">www.brindlesky.com</p>
</section>

</body>
</html>
```